Harrow Tavern & Grille Menu Makeover

I am looking for a professional look to update our current menu. We are an independently owned sports bar and grill. Up to this point, I have done all of my own graphic designing. I am looking for something classy/family oriented. We are a very family friendly sports bar that offers a wide variety of menu options. Our website is www.harrowtavernco.example. This may help you get more of a feel for what type of place we are and what we offer. Our menu is listed on the website. My current menu is 8.5x14 inserts that feature a cover page, 4 inside pages and a back page. I would like something a little more condensed than this. Possibly a large tri-fold menu? I am open to all new ideas. I do have some pictures on my menu now, and would like to continue using a few pictures to feature some of my items. I would like something that is in a format that gives me the option to change items and prices on my own in the future. I would also like it to feature, or inform my patrons about our technology that we offer. We offer online ordering and we are a "verified venue" with Brewvoke.( a social site for craft beer lovers).

Industry/Entity Type

Sports Bar

Requirements
Nice to have
• Nice to have some pictures, but does not have to. We do feature 9 different beers on tap. A lot of them are local craft beers from the state of Kansas. Not sure if that is something we can feature, but it is a nice talking point. All of our tables and bar are hand built. With a rich mahogany finish on all of our woodwork, some type of "woodgrain" look into the menu would be nice.

```html
<!DOCTYPE html>
<html lang="en">
<head>
<meta charset="utf-8">
<title>Harrow Tavern &amp; Grille — Menu</title>
<link rel="stylesheet" href="https://fonts.googleapis.com/css2?family=Cinzel:wght@700&family=Oswald:wght@300;400&display=swap">
<style>
  :root {
    --mahogany-dark: #3a1208;
    --mahogany: #6e2814;
    --mahogany-light: #8a3a1e;
    --parchment: #dcc498;
    --parchment-mid: #c9a874;
    --parchment-edge: #9c7444;
    --ink: #1e150c;
    --ink-soft: #2e2216;
  }
  * { margin: 0; padding: 0; box-sizing: border-box; }
  html, body { width: 850px; height: 1200px; overflow: hidden; }
  body { background: var(--mahogany-dark); }
  .menu {
    position: relative; width: 850px; height: 1200px; overflow: hidden;
    background:
      repeating-linear-gradient(90deg, rgba(0,0,0,0.10) 0 3px, transparent 3px 19px, rgba(255,255,255,0.03) 19px 23px, transparent 23px 41px),
      linear-gradient(90deg, var(--mahogany-dark), var(--mahogany) 30%, var(--mahogany-light) 55%, var(--mahogany) 80%, var(--mahogany-dark));
    color: var(--ink);
  }
  .parchment { position: absolute; left: 0; top: 0; }
  .section-title {
    position: absolute; font-family: "Cinzel", serif; font-weight: 700;
    font-size: 35px; color: var(--ink); letter-spacing: 0.5px; line-height: 1;
  }
  .item { position: absolute; width: 320px; font-family: "Oswald", sans-serif; text-transform: uppercase; }
  .item-name { font-weight: 400; font-size: 14.5px; line-height: 1.05; color: var(--ink); }
  .item-desc { font-weight: 300; font-size: 8.6px; line-height: 1.35; color: var(--ink-soft); }
  .item-price { font-weight: 400; font-size: 7.5px; letter-spacing: 0.8px; color: var(--ink); line-height: 1.2; }
  .divider { position: absolute; left: 200px; width: 448px; height: 12px; }
</style>
</head>
<body>
<main class="menu">
  <svg class="parchment" width="850" height="1200" viewBox="0 0 850 1200">
    <defs>
      <radialGradient id="paper" cx="50%" cy="50%" r="60%">
        <stop offset="0" stop-color="#e0c99e"/>
        <stop offset="0.7" stop-color="#cdae7c"/>
        <stop offset="1" stop-color="#9c7444"/>
      </radialGradient>
      <radialGradient id="plate" cx="50%" cy="50%" r="50%">
        <stop offset="0" stop-color="#b89668" stop-opacity="0.55"/>
        <stop offset="1" stop-color="#b89668" stop-opacity="0"/>
      </radialGradient>
      <radialGradient id="tacos" cx="50%" cy="50%" r="50%">
        <stop offset="0" stop-color="#c9a060" stop-opacity="0.6"/>
        <stop offset="0.6" stop-color="#9aa060" stop-opacity="0.3"/>
        <stop offset="1" stop-color="#9aa060" stop-opacity="0"/>
      </radialGradient>
    </defs>
    <polygon fill="url(#paper)" points="62,92 110,80 170,86 230,76 300,84 380,78 470,86 560,80 650,88 720,76 760,90 810,82 800,110 806,160 798,230 804,320 796,420 806,500 798,560 804,640 798,740 806,820 798,900 804,980 796,1040 802,1090 790,1104 730,1098 660,1106 580,1096 500,1104 420,1098 340,1106 260,1098 180,1104 110,1096 66,1100 58,1060 50,980 58,900 48,820 56,740 46,660 54,580 48,500 56,420 48,340 56,260 48,180 56,120"/>
    <ellipse role="img" aria-label="Faded photo of onion rings and greens on a plate" cx="470" cy="330" rx="340" ry="230" fill="url(#plate)"/>
    <ellipse role="img" aria-label="Faded photo of crispy tacos with lettuce and cheese" cx="480" cy="1010" rx="380" ry="200" fill="url(#tacos)"/>
  </svg>

  <h2 class="section-title" style="left:94px;top:164px;">BURGERS</h2>

  <div class="item" style="left:98px;top:209px;">
    <div class="item-name">Black Angus Blue Cheese &amp; Bacon Burger</div>
    <div class="item-desc">A juicy half pound burger with crumbled blue cheese and crisp bacon served<br>on a toasted bun with lettuce, tomatoes, red onions and pickles.</div>
    <div class="item-price">8.99</div>
  </div>
  <div class="item" style="left:98px;top:265px;">
    <div class="item-name">All-American Cheeseburger</div>
    <div class="item-desc">A half pound classic cheeseburger.</div>
    <div class="item-price">7.99</div>
  </div>
  <div class="item" style="left:98px;top:309px;">
    <div class="item-name">San Francisco Burger</div>
    <div class="item-desc">A half pound burger topped with provolone cheese, crisp bacon, grilled onions,<br>guacamole, mushrooms and black olives.</div>
    <div class="item-price">8.99</div>
  </div>
  <div class="item" style="left:98px;top:365px;">
    <div class="item-name">French Dip Burger</div>
    <div class="item-desc">A half pound burger topped with swiss cheese and smothered in grilled onions.<br>Served on a ciabatta bun with a side of French onion soup.</div>
    <div class="item-price">8.99</div>
  </div>
  <div class="item" style="left:98px;top:421px;">
    <div class="item-name">Gourmet Patty Melt</div>
    <div class="item-desc">A half pound all beef patty stacked high with swiss cheese, grilled onions,<br>and tomato! Served open faced on toasted rye.</div>
    <div class="item-price">7.99</div>
  </div>

  <div class="item" style="left:427px;top:209px;width:340px;">
    <div class="item-name">Harrow Double Bacon Cheeseburger</div>
    <div class="item-desc">Two mouth watering half pound patties layered with crisp bacon, American cheese,<br>lettuce, tomatoes, red onions, and pickles.</div>
    <div class="item-price">9.99</div>
  </div>
  <div class="item" style="left:427px;top:265px;width:340px;">
    <div class="item-name">Quesadilla Burger</div>
    <div class="item-desc">A crispy flour tortilla stuffed with ground beef, jack and cheddar cheese,<br>barbeque sauce, grilled peppers and onions, topped with lettuce pickles and<br>red onions.</div>
    <div class="item-price">9.99</div>
  </div>
  <div class="item" style="left:427px;top:333px;width:340px;">
    <div class="item-name">Pepper Jack Cheeseburger</div>
    <div class="item-desc">A half pound burger topped with pepper jack cheese, grilled jalapeños and bacon.</div>
    <div class="item-price">8.99</div>
  </div>
  <div class="item" style="left:427px;top:377px;width:340px;">
    <div class="item-name">Texas Burger</div>
    <div class="item-desc">A half pounder decked out with American cheese, tangy barbecue sauce and<br>crispy onion rings.</div>
    <div class="item-price">8.99</div>
  </div>
  <div class="item" style="left:427px;top:433px;width:340px;">
    <div class="item-name">Bourbon Burger</div>
    <div class="item-desc">A half pounder smothered in pepper jack cheese, bourbon glaze, and blooming<br>onion petals.</div>
    <div class="item-price">8.99</div>
  </div>

  <svg class="divider" style="top:522px;" viewBox="0 0 448 12">
    <line x1="0" y1="6" x2="448" y2="6" stroke="#1e150c" stroke-width="1.2"/>
    <ellipse role="img" aria-label="Small scroll ornament" cx="224" cy="6" rx="16" ry="6" fill="#1e150c"/>
  </svg>

  <h2 class="section-title" style="left:94px;top:566px;">PASTA</h2>

  <div class="item" style="left:98px;top:609px;">
    <div class="item-name">Lasagna</div>
    <div class="item-desc">Harrow famous homemade lasagna!</div>
    <div class="item-price">Small 7.99 / Large 9.99</div>
  </div>
  <div class="item" style="left:98px;top:653px;">
    <div class="item-name">Italian Spaghetti &amp; Meatballs</div>
    <div class="item-desc">This classic is topped with shredded parmesan cheese.</div>
    <div class="item-price">Small 6.99 / Large 8.99</div>
  </div>
  <div class="item" style="left:427px;top:609px;width:340px;">
    <div class="item-name">Fettuccini Alfredo</div>
    <div class="item-desc">Fettuccini topped with creamy alfredo and blended Normandy vegetables served<br>with your choice of chicken or grilled shrimp.</div>
    <div class="item-price">Small 7.99 / Large 9.99</div>
  </div>
  <div class="item" style="left:427px;top:665px;width:340px;">
    <div class="item-name">Chicken Parmesan</div>
    <div class="item-desc">Tender grilled chicken breast topped with marinara sauce and parmesan cheese<br>served on a bed of spaghetti</div>
    <div class="item-price">Small 7.99 / Large 9.99</div>
  </div>

  <svg class="divider" style="top:758px;" viewBox="0 0 448 12">
    <line x1="0" y1="6" x2="448" y2="6" stroke="#1e150c" stroke-width="1.2"/>
    <ellipse role="img" aria-label="Small scroll ornament" cx="224" cy="6" rx="16" ry="6" fill="#1e150c"/>
  </svg>

  <h2 class="section-title" style="left:88px;top:808px;">MEXICAN</h2>

  <div class="item" style="left:94px;top:855px;width:310px;">
    <div class="item-name">Taco Bowl</div>
    <div class="item-desc">Your choice of chicken or beef in a fried 12 inch tortilla bowl, topped with<br>lettuce, jack and cheddar cheese, tomatoes and sour cream.</div>
    <div class="item-price">8.99</div>
  </div>
  <div class="item" style="left:94px;top:911px;width:310px;">
    <div class="item-name">Six Pack Tacos</div>
    <div class="item-desc">Six crispy tacos stuffed with beef, cheese, lettuce and tomatoes.</div>
    <div class="item-price">8.99</div>
  </div>
  <div class="item" style="left:94px;top:955px;width:310px;">
    <div class="item-name">Chimichanga</div>
    <div class="item-desc">A 12 inch flour tortilla deep fried and stuffed with your choice of chicken<br>or beef and jack and cheddar cheese. Smothered in melted jack cheese,<br>lettuce, and tomatoes.</div>
    <div class="item-price">8.99</div>
  </div>
  <div class="item" style="left:422px;top:855px;width:340px;">
    <div class="item-name">Southwest Chicken Sancho</div>
    <div class="item-desc">A bend of grilled chicken, cheese, lettuce, and salsa. Wrapped in a tortilla and<br>smothered with creamy alfredo sauce, jack and cheddar cheese and tomatoes.</div>
    <div class="item-price">8.99</div>
  </div>
  <div class="item" style="left:422px;top:911px;width:340px;">
    <div class="item-name">Loaded Chicken Quesadilla</div>
    <div class="item-desc">12 inch flour tortilla loaded with grilled chicken, barbecue sauce, crisp bacon and<br>grilled onions and peppers.</div>
    <div class="item-price">9.99</div>
  </div>
</main>
</body>
</html>
```